Walk Beside The River

Business Card design

Target Market(s)

People who require support in the commnity

Industry/Entity Type

Mental Health Support

Contact Information for Business Card

Mental Health Support Rosalind Tavener walkbesidetheriver@mailcove.com.au 0481 637 092 PO Box 926 Tallowood Heights QLD 4590

Colors
6B429C
8869AF
B7A5CE
E3DAEB
F3F0F8

Requirements
Must have
• Logo & details listed above
Should not have
• No red or orange

```html
<!DOCTYPE html>
<html lang="en">
<head>
<meta charset="utf-8">
<title>Walk Beside The River – Business Card</title>
<link rel="stylesheet" href="https://fonts.googleapis.com/css2?family=Open+Sans:wght@400;600;800&display=swap">
<style>
  :root {
    --stage: #2b2a30;
    --card: #1f1e23;
    --purple: #6B429C;
    --purple-soft: #8869AF;
    --yellow: #F2E92A;
    --white: #ffffff;
  }
  * { box-sizing: border-box; margin: 0; padding: 0; }
  html, body { width: 1200px; height: 780px; overflow: hidden; }
  body {
    background: var(--stage);
    font-family: "Open Sans", sans-serif;
    position: relative;
  }
  .card {
    position: absolute;
    top: 230px;
    width: 560px;
    height: 320px;
    border-radius: 22px;
    background: var(--card);
    border: 3px solid var(--yellow);
    overflow: hidden;
  }
  .card--back { left: 20px; }
  .card--front { left: 620px; }

  .back-pattern {
    position: absolute;
    inset: 0;
    background: linear-gradient(160deg, #3a393f 0%, #232227 40%, #1b1a1f 100%);
  }

  .front-art { position: absolute; inset: 0; }

  .title-tab {
    position: absolute;
    top: 0; right: 56px;
    width: 26px; height: 46px;
    background: var(--purple);
  }
  .person {
    position: absolute;
    top: 26px; right: 92px;
    text-align: right;
  }
  .person__name {
    font-weight: 800;
    font-size: 30px;
    line-height: 1;
    color: var(--yellow);
    white-space: nowrap;
  }
  .person__name span { color: var(--purple); }
  .person__role {
    margin-top: 6px;
    font-size: 14px;
    font-weight: 600;
    color: var(--white);
  }

  .brand {
    position: absolute;
    top: 28px; left: 30px;
    display: flex;
    align-items: center;
    gap: 10px;
  }
  .brand__dot {
    width: 72px; height: 72px;
    border-radius: 50%;
    background: var(--purple);
    flex: none;
  }
  .brand__name {
    width: 110px;
    font-size: 14px;
    font-weight: 600;
    line-height: 1.3;
    color: var(--white);
  }

  .details {
    position: absolute;
    top: 128px; left: 34px;
    color: var(--white);
    font-size: 15px;
    line-height: 1.45;
  }
  .details__service { font-size: 16px; }
  .details__person { font-size: 16px; margin-bottom: 4px; }
  .contact { list-style: none; }
  .contact li {
    display: flex;
    align-items: center;
    gap: 8px;
    white-space: nowrap;
  }
  .contact svg { width: 14px; height: 14px; flex: none; }
</style>
</head>
<body>

  <section class="card card--back" aria-label="Card back">
    <div class="back-pattern" role="img" aria-label="Repeating star pattern on a dark ground"></div>
  </section>

  <section class="card card--front" aria-label="Card front">
    <svg class="front-art" viewBox="0 0 554 314" preserveAspectRatio="none" aria-hidden="true">
      <path d="M150 314 C300 290 390 240 420 170 C445 110 480 80 554 60 L554 314 Z" fill="var(--purple)"/>
      <path d="M130 300 C230 300 330 270 390 215 C340 270 250 300 140 308 Z" fill="var(--yellow)"/>
    </svg>

    <div class="title-tab"></div>
    <div class="person">
      <p class="person__name">Dana <span>Holloway</span></p>
      <p class="person__role">CEO/Director</p>
    </div>

    <div class="brand">
      <span class="brand__dot"></span>
      <span class="brand__name">Walk Beside The River</span>
    </div>

    <div class="details">
      <p class="details__service">Mental Health Support</p>
      <p class="details__person">Rosalind Tavener</p>
      <ul class="contact">
        <li>
          <svg viewBox="0 0 24 24"><path fill="var(--yellow)" d="M6.6 10.8a15.1 15.1 0 0 0 6.6 6.6l2.2-2.2a1 1 0 0 1 1-.25 11.4 11.4 0 0 0 3.6.57 1 1 0 0 1 1 1V20a1 1 0 0 1-1 1A17 17 0 0 1 3 4a1 1 0 0 1 1-1h3.5a1 1 0 0 1 1 1c0 1.25.2 2.45.57 3.570a1 1 0 0 1-.25 1z"/></svg>
          0481 637 092
        </li>
        <li>
          <svg viewBox="0 0 24 24"><rect x="2" y="5" width="20" height="14" rx="2" fill="var(--yellow)"/><path d="M3 6l9 7 9-7" stroke="var(--card)" stroke-width="2" fill="none"/></svg>
          walkbesidetheriver@mailcove.com.au
        </li>
        <li>
          <svg viewBox="0 0 24 24"><path fill="var(--yellow)" d="M12 2a7 7 0 0 0-7 7c0 5 7 13 7 13s7-8 7-13a7 7 0 0 0-7-7zm0 9.5A2.5 2.5 0 1 1 12 6.5a2.5 2.5 0 0 1 0 5z"/></svg>
          PO Box 926 Tallowood Heights QLD 4590
        </li>
      </ul>
    </div>
  </section>

</body>
</html>
```